WE ARE BRIGHT SPARROW, building a full website with ecommerce

requirements:
CODED FOR SITEQUILL
ONLINE STORE FUNCTION WITH E-COMMERCE USING TRADEBLOOM
PAGEWAVE AND PICTOLANE LINKS

I need a website design for my organization, WE ARE BRIGHT SPARROW, a global empowerment movement elevating woman, and the world. The site's home page should reflect our mission, to empower women. It should have a strong, empowering feel, with minimalistic design.
Please see www.lunavelto.com and http://www.corvenhal.co/ for an inspiration on layout and feel.

**PLEASE SEE ATTACHMENT "LOGO MOCK UP" FOR LOGO. THIS IS NOT THE FINAL VECTOR FILE, BUT THIS LOOKS THE SAME AS THE FINAL LOGO.

HOME PAGE:
The first section of the home page should include a background image with our logo center.

You should include the following links to pages at the top right of the page:
MISSION
MANTRA
ARMOR
MEET BS (I would like "bs" to be our logo)
pagewave and pictolane links

As you scroll down the page, you should see the following sections, which correlate to the links to pages as written above. **SEE ATTACHED SKETCH "HOMEPAGE LAYOUT IDEA" FOR REFERENCE**

WHO WE ARE (correlates to the link Mission)

OUR MANTRA (correlates to the link Mantra)

OUR ARMOR (correlates to the link The Shirt)
(This is where we will sell a shirt (and other apparel) and need the e-commerce function)

MEET BRIGHT SPARROWS (correlates to the link Meet BS)

SHOW OFF YOUR SUPER POWERS (correlates to the pagewave and pictolane)

FEATURED BRIGHT SPARROW (no link on top right of page)

On the homepage, for each of the above sections, as you scroll down there should be an image, either in the background or framed, next to the title (WHO WE ARE, for example), as well as one sentence of small text explaining the title. The title (WHO WE ARE) and the one sentence should link to a page (ie WHO WE ARE + the one sentence links to the MISSION page). ** SEE ATTACHED SKETCH "HOMEPAGE SECTION IDEAS" FOR REFERENCE**

**PLEASE SEE ATTACHMENT "WEBSITE TITLE IDEAS" FOR A STARTING PLACE OF THE LOOK. These don't have to be exact, but they give you an idea of what I'm looking for.

**FONTS TYPOLD EXTRA BOLD AND TYPOLD BOOK 500 (WHICH SHOULD BE BOLDED MANUALLY) ARE ATTACHED**

Target Market(s)

Women, mainly in US

Industry/Entity Type

Social

Coding

Coded - Design and coding required

Number of Pages Required

5+ page

Font styles to use
Other font styles liked:
• Typol Extra Bold

Requirements
Must have
• CODED FOR SITEQUILL
• ONLINE STORE FUNCTION WITH E-COMMERCE USING TRADEBLOOM
• PAGEWAVE AND PICTOLANE LINKS
• Typold Extra Bold and Typold Book 500, attached
• please see description for all requirements
Nice to have
• please see description for all ideas
Should not have

```html
<!DOCTYPE html>
<html lang="en">
<head>
<meta charset="utf-8">
<title>We Are Bright Sparrow</title>
<link rel="stylesheet" href="https://fonts.googleapis.com/css2?family=Montserrat:wght@500;600;700;800&family=Nunito+Sans:wght@400;600&display=swap">
<style>
:root{
  --ink:#111111;
  --white:#ffffff;
  --teal:#4fdcc0;
  --sand:#ebe6da;
  --footer:#151515;
  --muted:#3a3a3a;
  --head:"Montserrat", Arial, sans-serif;
  --body:"Nunito Sans", Arial, sans-serif;
}
*{box-sizing:border-box;margin:0;padding:0}
html,body{width:1200px;height:3727px;overflow:hidden}
body{background:var(--white);font-family:var(--body);color:var(--ink);position:relative}
a{color:inherit;text-decoration:none}

/* mark: plain square with initials */
.mark{display:inline-flex;align-items:center;justify-content:center;border:3px solid currentColor;font-family:var(--head);font-weight:800;line-height:1}

/* header */
.site-header{height:100px;display:flex;align-items:center;justify-content:space-between;padding:0 88px 0 88px}
.brand{display:flex;align-items:center;gap:14px}
.brand .mark{width:50px;height:50px;font-size:17px}
.brand-name{font-family:var(--head);font-weight:800;font-size:17px;line-height:17px;letter-spacing:.5px}
.main-nav{display:flex;gap:28px;align-items:center;font-family:var(--head);font-weight:600;font-size:12px;letter-spacing:.6px}

/* hero */
.hero{position:absolute;top:100px;left:0;width:1200px;height:496px;background:linear-gradient(180deg,#3b3f44 0%,#5c6166 38%,#4a4d50 62%,#2a2b2d 100%);color:var(--white);text-align:center}
.hero-photo{position:absolute;inset:0;background:radial-gradient(ellipse at 28% 45%,rgba(190,195,200,.35),transparent 55%)}
.hero-inner{position:relative;padding-top:88px}
.hero .mark{width:96px;height:96px;font-size:32px;border-width:6px}
.hero-title{margin-top:38px;font-family:var(--head);font-weight:800;font-size:35px;line-height:48px;letter-spacing:1px}
.hero-form{margin:22px auto 0;display:flex;justify-content:center;gap:8px}
.field{width:298px;height:46px;background:var(--white);border:0;padding:0 18px;font-family:var(--body);font-size:14px;color:var(--ink)}
.btn{height:46px;background:var(--teal);color:var(--white);border:0;font-family:var(--head);font-weight:800;font-size:15px;letter-spacing:1px;padding:0 22px}

/* mission band */
.band{position:absolute;top:596px;left:0;width:1200px;height:179px;background:var(--teal);color:var(--white);display:flex;align-items:center;justify-content:space-between;padding:0 115px}
.band-text{font-family:var(--head);font-weight:500;font-size:24px;line-height:34px;letter-spacing:.6px;width:760px}
.band-text strong{font-weight:800}
.fly-box{width:160px;height:90px;border:2px solid var(--white);display:flex;align-items:center;justify-content:center;gap:14px}
.fly-box .mark{width:46px;height:46px;font-size:15px}
.fly-box span{font-family:var(--head);font-weight:800;font-size:16px;line-height:16px}
.fly-box b{display:block;font-size:32px;line-height:32px}

/* sections grid */
.sections{position:absolute;top:783px;left:10px;width:1180px;display:grid;grid-template-columns:585px 585px;grid-auto-rows:415px;gap:10px}
.panel{background:var(--sand);padding:62px 80px 0 80px}
.panel-head{display:flex;align-items:center;gap:20px;margin-left:20px}
.panel-head .mark{width:92px;height:92px;font-size:26px;border-width:6px;flex:none}
.panel-title{font-family:var(--head);font-weight:800;font-size:38px;line-height:36px;letter-spacing:.3px}
.panel-title small{display:block;font-size:22px;line-height:26px}
.panel-copy{margin-top:42px;font-size:13px;line-height:21px;color:var(--muted);width:440px}
.photo{position:relative}
.photo-1{background:linear-gradient(135deg,#c9d2da,#8a9aa8 55%,#5b6670)}
.photo-2{background:linear-gradient(135deg,#e9ecdf,#b8cf66 40%,#6f7a88)}
.photo-3{background:linear-gradient(135deg,#1f88b4,#2a9ecb 50%,#12607f)}
.photo-4{background:linear-gradient(135deg,#e6e8ec,#a9b0bc 50%,#6e6a70)}
.photo-5{background:linear-gradient(135deg,#6a6862,#8c857a 50%,#3d3f41);display:flex;align-items:center;justify-content:center;gap:40px;color:var(--white);font-family:var(--head);font-weight:800;font-size:24px;letter-spacing:1px}
.photo-6{background:linear-gradient(135deg,#f1eee8,#d7cbb7 50%,#a6977f)}

/* footer */
.site-footer{position:absolute;top:3332px;left:0;width:1200px;height:395px;background:var(--footer);color:var(--white);text-align:center;padding-top:56px}
.footer-social{font-family:var(--head);font-weight:600;font-size:12px;letter-spacing:.8px;display:flex;gap:18px;justify-content:center}
.footer-form{margin-top:24px;display:flex;justify-content:center;gap:8px}
.footer-form .field{width:312px;height:42px;font-size:12px;color:#8a8a8a}
.footer-form .btn{height:42px;width:168px;font-size:15px}
.footer-nav{margin-top:30px;display:flex;gap:34px;justify-content:center;font-family:var(--head);font-weight:600;font-size:12px;letter-spacing:.6px}
.copyright{margin-top:14px;font-size:13px}
.site-footer .mark{margin-top:44px;width:86px;height:86px;font-size:26px;border-width:6px}
</style>
</head>
<body>

<header class="site-header">
  <a class="brand" href="#">
    <span class="mark">BS</span>
    <span class="brand-name">WE ARE<br>BRIGHT<br>SPARROW</span>
  </a>
  <nav class="main-nav">
    <a href="#mission">MISSION</a>
    <a href="#mantra">MANTRA</a>
    <a href="#meet">MEET BS</a>
    <a href="#armor">THE SHIRT</a>
    <a href="#">PAGEWAVE</a>
    <a href="#">PICTOLANE</a>
  </nav>
</header>

<section class="hero">
  <div class="hero-photo" role="img" aria-label="Woman seen from behind with raised arms above a misty mountain landscape"></div>
  <div class="hero-inner">
    <span class="mark">BS</span>
    <h1 class="hero-title">WE ARE BRIGHT SPARROW<br>AND I WILL CONQUER THE WORLD</h1>
    <form class="hero-form">
      <input class="field" type="email" value="brightsparrow@email.com" aria-label="Email">
      <button class="btn" type="button">LET'S FLY</button>
    </form>
  </div>
</section>

<section class="band">
  <p class="band-text"><strong>WE ARE BRIGHT SPARROW</strong> IS A GLOBAL EMPOWERMENT MOVEMENT ELEVATING WOMEN... AND THE WORLD.</p>
  <a class="fly-box" href="#">
    <span class="mark">BS</span>
    <span>LET'S<b>FLY</b></span>
  </a>
</section>

<main class="sections">
  <article class="panel" id="mission">
    <div class="panel-head"><span class="mark">BS</span><h2 class="panel-title">WHO<br>WE<br>ARE</h2></div>
    <p class="panel-copy">We are a worldwide circle of women who lift one another up. We share stories, skills and courage so every member can rise higher, speak louder and lead with heart. Our mission is simple: help each woman find her strength and use it to change her world for good.</p>
  </article>
  <div class="photo photo-1" role="img" aria-label="Portrait of a confident businesswoman with arms crossed in a bright office"></div>

  <div class="photo photo-2" role="img" aria-label="Smiling woman in a grey blazer seated on a green chair"></div>
  <article class="panel" id="mantra">
    <div class="panel-head"><span class="mark">BS</span><h2 class="panel-title">OUR<br>MANTRA</h2></div>
    <p class="panel-copy">We are a worldwide circle of women who lift one another up. We share stories, skills and courage so every member can rise higher, speak louder and lead with heart. Our mission is simple: help each woman find her strength and use it to change her world for good.</p>
  </article>

  <article class="panel" id="meet">
    <div class="panel-head"><span class="mark">BS</span><h2 class="panel-title" style="font-size:33px;line-height:33px">MEET<br>BRIGHT<br>SPARROWS</h2></div>
    <p class="panel-copy">We are a worldwide circle of women who lift one another up. We share stories, skills and courage so every member can rise higher, speak louder and lead with heart. Our mission is simple: help each woman find her strength and use it to change her world for good.</p>
  </article>
  <div class="photo photo-3" role="img" aria-label="Smiling young woman in a white shirt against a blue wall"></div>

  <div class="photo photo-4" role="img" aria-label="Businesswoman in a grey jacket with colleagues talking behind her"></div>
  <article class="panel" id="armor">
    <div class="panel-head"><span class="mark">BS</span><h2 class="panel-title">OUR<br>ARMOR</h2></div>
    <p class="panel-copy">We are a worldwide circle of women who lift one another up. We share stories, skills and courage so every member can rise higher, speak louder and lead with heart. Our mission is simple: help each woman find her strength and use it to change her world for good.</p>
  </article>

  <article class="panel" id="powers">
    <div class="panel-head"><span class="mark">BS</span><h2 class="panel-title"><small>SHOW OFF YOUR</small>SUPER<br>POWERS</h2></div>
    <p class="panel-copy">We are a worldwide circle of women who lift one another up. We share stories, skills and courage so every member can rise higher, speak louder and lead with heart. Our mission is simple: help each woman find her strength and use it to change her world for good.</p>
  </article>
  <div class="photo photo-5" role="img" aria-label="Woman working in a modern office, dimmed behind social links">
    <a href="#">PAGEWAVE</a><a href="#">PICTOLANE</a>
  </div>

  <div class="photo photo-6" role="img" aria-label="Smiling woman in a white blouse in a light room"></div>
  <article class="panel" id="featured">
    <div class="panel-head"><span class="mark">BS</span><h2 class="panel-title" style="font-size:33px;line-height:33px">FEATURED<br>BRIGHT<br>SPARROW</h2></div>
    <p class="panel-copy">We are a worldwide circle of women who lift one another up. We share stories, skills and courage so every member can rise higher, speak louder and lead with heart. Our mission is simple: help each woman find her strength and use it to change her world for good.</p>
  </article>
</main>

<footer class="site-footer">
  <div class="footer-social"><a href="#">PAGEWAVE</a><a href="#">PICTOLANE</a></div>
  <form class="footer-form">
    <input class="field" type="email" value="Enter Email" aria-label="Email">
    <button class="btn" type="button">SUBMIT</button>
  </form>
  <nav class="footer-nav">
    <a href="#mission">MISSION</a>
    <a href="#mantra">MANTRA</a>
    <a href="#meet">MEET BS</a>
    <a href="#armor">THE SHIRT</a>
  </nav>
  <p class="copyright">Copyright © 2017. We Are Bright Sparrow. All rights reserved</p>
  <span class="mark">BS</span>
</footer>

</body>
</html>
```